Flyer for spiritual retreat (yoga, meditation, reiki, raw food)

I would like a flyer to promote my upcoming retreat and a matching Facebook banner.

The name of the retreat is "OutBloom the Spirit" and the tagline is "retreat into you"

The activities in the retreat include daily meditation, ecstatic dance, spiritual development workshops on intuition, energy healing etc and a reiki session is included.

I would like a flyer designed to promote this, something that is editable as I will be running this multiple times and will need to adjust the flyer to add the dates etc each time.

edit: add that here will be fully catered raw food and juices, and that the retreat price includes all accomodation, meals and workshops.

Please contact me if you need further info. Please also visit my website www.marlavosk.com and www.pagenest.com/koruhaven to see my current events and promotions.

Thank you,

Marla

Reason: Hi all, thank you all for your submissions. Apologies as I am traveling and do not have much access to internet and will review your submissions and provide feedback as soon as possible. Kind regards, Marla.

Target Market(s)

People who like meditation, yoga, fans of tomas brenner and wendell marsh, those interested in personal and spiritual development.

Industry/Entity Type

Health And Wellness

Requirements
Must have
• Please put the included reiki session as as added bonus. Something like "BONUS 30 minute reiki healing session" in a little star/banner/something that stands out.
• Please emphasise the "light" part of OutBloom as I am going for a play on words between in the light and enlightenment.
• Please include placeholder text for place, location, time
• Placeholder for price
• My name (see attached file - can change colour to suit) and website (www.marlavosk.com)
Nice to have
• I prefer rounded designs, curves rather than block designs.
Should not have
• Koru Haven logo

```html
<!DOCTYPE html>
<html lang="en">
<head>
<meta charset="utf-8">
<title>OutBloom the Spirit — Retreat Flyer &amp; Banner</title>
<link rel="stylesheet" href="https://fonts.googleapis.com/css2?family=Pinyon+Script&family=Raleway:wght@300&family=Crimson+Text:ital,wght@0,400;0,600;1,400;1,700&family=Montserrat:wght@700&display=swap">
<style>
  :root {
    --page: #e8e6e2;
    --sky-top: #7ba4d7;
    --sky-light: #dde7f4;
    --sky-mid: #7c9fd2;
    --sky-deep: #3f5e91;
    --ink-white: #ffffff;
    --ink-soft: #f2f6fc;
    --band-dark: #222a38;
    --script: "Pinyon Script", cursive;
    --sans: "Raleway", sans-serif;
    --serif: "Crimson Text", serif;
    --label: "Montserrat", sans-serif;
  }
  * { margin: 0; padding: 0; box-sizing: border-box; }
  html, body { width: 848px; height: 1200px; overflow: hidden; background: var(--page); }
  .canvas { position: relative; width: 848px; height: 1200px; }

  /* Banner */
  .banner {
    position: absolute; left: 44px; top: 46px; width: 759px; height: 287px;
    background: linear-gradient(to bottom, var(--sky-top) 0%, #a9c3e6 35%, var(--sky-light) 58%, #b4c9e9 70%, var(--sky-mid) 84%, var(--sky-deep) 100%);
    color: var(--ink-white);
  }
  .title { position: absolute; font-family: var(--script); font-weight: 400; line-height: 1; color: var(--ink-white); white-space: nowrap; }
  .tagline { position: absolute; font-family: var(--sans); font-weight: 300; letter-spacing: 0.5px; color: var(--ink-white); white-space: nowrap; }
  .banner .title-line1 { left: 136px; top: 66px; font-size: 76px; }
  .banner .title-line2 { left: 180px; top: 140px; font-size: 72px; }
  .banner .tagline { left: 336px; top: 216px; font-size: 26px; }

  /* Flyer */
  .flyer {
    position: absolute; left: 148px; top: 384px; width: 549px; height: 781px;
    background: linear-gradient(to bottom, #86acdb 0%, #7299cc 24%, var(--sky-deep) 38%, #5273a8 50%, #7f9fd2 68%, #a9c0e6 85%, #c3d5f0 98%);
    color: var(--ink-white);
    overflow: hidden;
  }
  .flyer .title-line1 { left: 34px; top: 48px; font-size: 70px; }
  .flyer .title-line2 { left: 76px; top: 116px; font-size: 66px; }
  .flyer .tagline { left: 259px; top: 193px; font-size: 21px; }

  .intro {
    position: absolute; left: 17px; top: 236px; width: 232px;
    font-family: var(--serif); font-style: italic; font-size: 15px; line-height: 23px;
    color: var(--ink-soft);
  }
  .intro strong { font-weight: 700; }
  .brace { position: absolute; left: 244px; top: 240px; width: 30px; height: 208px; }

  .benefits { position: absolute; left: 287px; top: 236px; list-style: none; font-family: var(--serif); font-size: 16.5px; color: var(--ink-soft); }
  .benefits li { height: 36px; line-height: 24px; white-space: nowrap; }
  .benefits li::before { content: "✻"; font-size: 12px; margin-right: 6px; vertical-align: 1px; }

  .bonus {
    position: absolute; left: 0; width: 100%; top: 458px; text-align: center;
    font-family: var(--serif); font-weight: 600; font-size: 17.5px; color: var(--ink-white);
  }
  .bonus-rule { position: absolute; left: 110px; top: 486px; width: 330px; height: 6px; }

  .details { position: absolute; left: 17px; top: 508px; font-family: var(--label); font-size: 10.5px; letter-spacing: 0.8px; color: var(--ink-white); }
  .details dt { display: flex; height: 30px; line-height: 16px; }
  .details dt span:first-child { width: 52px; }

  .signature {
    position: absolute; left: 362px; top: 496px; width: 170px; height: 56px;
    background: linear-gradient(to right, rgba(40,50,70,0.35), rgba(40,50,70,0.15));
    border-radius: 28px;
  }
  .contact { position: absolute; right: 17px; top: 568px; text-align: right; font-family: var(--serif); font-size: 17.5px; line-height: 24px; color: var(--ink-white); }
  .contact .social::before {
    content: ""; display: inline-block; width: 14px; height: 14px; background: var(--ink-white);
    margin-right: 5px; vertical-align: -1px;
  }

  .lotus-figure {
    position: absolute; left: 120px; top: 596px; width: 306px; height: 168px;
    background: radial-gradient(ellipse at 50% 70%, rgba(255,255,255,0.55) 0%, rgba(255,255,255,0.25) 45%, rgba(255,255,255,0) 72%);
  }
  .base-band { position: absolute; left: 0; bottom: 0; width: 100%; height: 17px; background: var(--band-dark); }
</style>
</head>
<body>
<main class="canvas">

  <section class="banner" aria-label="Social banner">
    <h1 class="title title-line1">OutBloom</h1>
    <p class="title title-line2">the Spirit</p>
    <p class="tagline">RETREAT INTO YOU</p>
  </section>

  <section class="flyer" aria-label="Retreat flyer">
    <h2 class="title title-line1">OutBloom</h2>
    <p class="title title-line2">the Spirit</p>
    <p class="tagline">RETREAT INTO YOU</p>

    <p class="intro">Leave your stresses and worries behind. Come immerse yourself in the bliss of the Transcendental Self. Learn how to integrate this level of awareness into daily living for greater peace, success and happiness in life. In this special <strong>all inclusive</strong> retreat you will gain the benefits of:</p>

    <svg class="brace" viewBox="0 0 30 208" aria-hidden="true">
      <path d="M2 2 C16 4 14 20 14 40 L14 88 C14 98 18 102 28 104 C18 106 14 110 14 120 L14 168 C14 188 16 204 2 206"
            fill="none" stroke="#ffffff" stroke-width="1.5"/>
    </svg>

    <ul class="benefits">
      <li>Daily Meditation Practice</li>
      <li>Ecstatic Dance</li>
      <li>Spiritual Development</li>
      <li>Enhanced Intuition</li>
      <li>Energy Healing</li>
      <li>Fully Catered Raw Food &amp; Juices</li>
    </ul>

    <p class="bonus">BONUS 30 Minute Reiki Healing Session</p>
    <svg class="bonus-rule" viewBox="0 0 330 6" aria-hidden="true">
      <path d="M0 3 Q165 0 330 3 Q165 6 0 3 Z" fill="#ffffff"/>
    </svg>

    <dl class="details">
      <dt><span>DATE</span><span>:</span></dt>
      <dt><span>PLACE</span><span>:</span></dt>
      <dt><span>TIME</span><span>:</span></dt>
      <dt><span>COST</span><span>:</span></dt>
    </dl>

    <div class="signature" role="img" aria-label="Marla Vosk handwritten signature"></div>
    <div class="contact">
      <p>www.marlavosk.com</p>
      <p class="social">koruhaven</p>
    </div>

    <div class="lotus-figure" role="img" aria-label="Seated meditation statue on a white line-art lotus flower"></div>
    <div class="base-band"></div>
  </section>

</main>
</body>
</html>
```